Graphic designs required for HR consulting Website

We need to items designed to be used on our website and in presentations.
Please view our website for design ideas.
http://www.brightmoor.com.au.42.vexaloft.pw
See attached Powerpoint doc for more info.
InfoGraphic 1
Needs to be turned into an infographic that will be embedded into the Brightmoor HR website.
The fonts should be Helvetica Neue and should have the look and feel of the website.
InfoGraphic 2
Needs to be turned into an infographic that will be embedded into the Brightmoor HR website and used in PPT and WORD proposals.
The fonts should be Helvetica Neue, the look and
feel should be consistent with the first infographic.
A mountain analogy is needed that shows how the sequence of services will come together to take businesses on the journey to becoming great.
2 versions of the same information are shown on the following slides. The first is for ease of visibility, the second is to show the sequence of services on the journey.
Samples of possible design ideas for inspiration are at bottom of ppt.
Consulting
- Helvetica

```html
<!DOCTYPE html>
<html lang="en">
<head>
<meta charset="utf-8">
<title>The Journey to Greatness</title>
<link rel="stylesheet" href="https://fonts.googleapis.com/css2?family=Inter+Tight:wght@300;400;500&family=Montserrat:wght@600&display=swap">
<style>
  :root {
    --paper: #f8f6f2;
    --navy-text: #0b2a47;
    --blue-text: #2a8fd0;
    --rule: #b9c3cc;
    --bar-navy: #0c2f4f;
    --bar-blue: #2a8fd0;
    --tier-bright: #2b90d2;
    --tier-bright-side: #0a6aa8;
    --tier-deep: #053f66;
    --tier-deep-side: #02213b;
    --tier-top: #06304f;
    --label-white: #ffffff;
  }
  html, body {
    margin: 0;
    padding: 0;
    width: 1200px;
    height: 847px;
    overflow: hidden;
    background: var(--paper);
  }
  .canvas {
    display: block;
    width: 1200px;
    height: 847px;
    font-family: "Inter Tight", "Helvetica Neue", Helvetica, Arial, sans-serif;
  }
  .rule { stroke: var(--rule); stroke-width: 1.3; }
  .bar-navy { fill: var(--bar-navy); }
  .bar-blue { fill: var(--bar-blue); }
  .service-title { font-size: 21px; font-weight: 500; letter-spacing: -0.3px; }
  .service-text { font-size: 20.5px; font-weight: 300; letter-spacing: -0.2px; }
  .navy { fill: var(--navy-text); }
  .blue { fill: var(--blue-text); }
  .end { text-anchor: end; }
  .tier-name { fill: var(--label-white); font-size: 30px; font-weight: 300; letter-spacing: -0.2px; }
  .tier-number { fill: var(--label-white); font-family: "Montserrat", "Helvetica Neue", Arial, sans-serif; font-size: 56px; font-weight: 600; letter-spacing: -1px; }
</style>
</head>
<body>
<svg class="canvas" viewBox="0 0 1500 1059" xmlns="http://www.w3.org/2000/svg" role="img" aria-label="Five tier pyramid of services on the journey to greatness">
  <rect width="1500" height="1059" fill="var(--paper)"/>

  <g class="rules">
    <line class="rule" x1="625" y1="219" x2="890" y2="219"/>
    <line class="rule" x1="205" y1="268" x2="485" y2="268"/>
    <line class="rule" x1="497" y1="316" x2="806" y2="316"/>
    <line class="rule" x1="104" y1="386" x2="384" y2="386"/>
    <line class="rule" x1="397" y1="434" x2="700" y2="434"/>
    <line class="rule" x1="298" y1="602" x2="548" y2="602"/>
    <line class="rule" x1="10" y1="735" x2="286" y2="735"/>
    <line class="rule" x1="298" y1="921" x2="612" y2="921"/>
  </g>

  <g class="pyramid">
    <polygon points="550,608 1020,882 1025,1040 460,712" fill="var(--tier-deep)"/>
    <polygon points="1020,882 1392,632 1472,740 1025,1040" fill="var(--tier-deep-side)"/>
    <polygon points="640,505 1017,725 1020,882 550,608" fill="var(--tier-bright)"/>
    <polygon points="1017,725 1312,525 1392,632 1020,882" fill="var(--tier-bright-side)"/>
    <polygon points="728,405 1012,568 1017,725 640,505" fill="var(--tier-deep)"/>
    <polygon points="1012,568 1233,420 1312,525 1017,725" fill="var(--tier-deep-side)"/>
    <polygon points="818,302 1005,410 1012,568 728,405" fill="var(--tier-bright)"/>
    <polygon points="1005,410 1157,313 1233,420 1012,568" fill="var(--tier-bright-side)"/>
    <polygon points="907,200 1000,252 1005,410 818,302" fill="var(--tier-top)"/>
    <polygon points="1000,252 1075,205 1157,313 1005,410" fill="var(--tier-deep-side)"/>
    <polygon points="995,100 1000,252 907,200" fill="var(--tier-bright)"/>
    <polygon points="995,100 1075,205 1000,252" fill="var(--tier-bright-side)"/>
  </g>

  <g class="tier-names">
    <text class="tier-name" transform="translate(866,274) rotate(33)">
      <tspan x="42" y="-36">The</tspan>
      <tspan x="0" y="0">Embedding</tspan>
      <tspan x="4" y="38">Greatness</tspan>
    </text>
    <text class="tier-name" transform="translate(817,381) rotate(32)">
      <tspan x="0" y="0">Developing</tspan>
      <tspan x="8" y="39">Greatness</tspan>
    </text>
    <text class="tier-name" transform="translate(774,509) rotate(32)">
      <tspan x="0" y="0">Resourcing</tspan>
      <tspan x="8" y="39">Greatness</tspan>
    </text>
    <text class="tier-name" transform="translate(657,611) rotate(31)">The Heart of Greatness</text>
    <text class="tier-name" transform="translate(580,709) rotate(32)">
      <tspan x="0" y="0">The Foundations of Greatness:</tspan>
      <tspan x="-64" y="42">Trusted advice and compliance support</tspan>
    </text>
  </g>

  <g class="tier-numbers">
    <text class="tier-number" transform="translate(1040,336) rotate(-33)">05</text>
    <text class="tier-number" transform="translate(1075,460) rotate(-33)">04</text>
    <text class="tier-number" transform="translate(1115,596) rotate(-33)">03</text>
    <text class="tier-number" transform="translate(1157,728) rotate(-33)">02</text>
    <text class="tier-number" transform="translate(1207,854) rotate(-33)">01</text>
  </g>

  <rect class="bar-navy" x="613" y="115" width="11" height="121"/>
  <text class="service-text navy">
    <tspan x="641" y="155">On-site strategic and</tspan>
    <tspan x="641" y="181">operational support to</tspan>
    <tspan x="641" y="206">sustain your journey</tspan>
  </text>

  <rect class="bar-blue" x="485" y="170" width="11" height="167"/>
  <text class="service-title blue end" x="458" y="203">Build Bright Teams</text>
  <text class="service-text blue end">
    <tspan x="458" y="231">Leadership</tspan>
    <tspan x="458" y="252">development programs</tspan>
  </text>
  <text class="service-title blue" x="514" y="276">Grow Bright Leaders</text>
  <text class="service-text blue" x="514" y="301">Leadership coaching</text>

  <rect class="bar-navy" x="384" y="289" width="12" height="166"/>
  <text class="service-title navy end" x="357" y="323">Culture Lens</text>
  <text class="service-text navy end">
    <tspan x="357" y="350">Pre-employment</tspan>
    <tspan x="357" y="370">assessments</tspan>
  </text>
  <text class="service-title navy" x="413" y="371">Hire Support</text>
  <text class="service-text navy">
    <tspan x="413" y="399">The expertise to select</tspan>
    <tspan x="413" y="420">great people</tspan>
  </text>

  <rect class="bar-blue" x="286" y="457" width="12" height="493"/>
  <text class="service-title blue" x="315" y="511">Step 1: Defining greatness</text>
  <text class="service-text blue">
    <tspan x="315" y="539">Business strategy, KPIs,</tspan>
    <tspan x="315" y="562">behaviours and role</tspan>
    <tspan x="315" y="585">clarity</tspan>
  </text>
  <text class="service-title blue end">
    <tspan x="261" y="642">Step 2:</tspan>
    <tspan x="261" y="667">Measuring Greatness</tspan>
  </text>
  <text class="service-text blue end">
    <tspan x="263" y="694">Creating a culture</tspan>
    <tspan x="263" y="717">of accountability</tspan>
  </text>
  <text class="service-title blue">
    <tspan x="312" y="829">Step 3:</tspan>
    <tspan x="312" y="855">Rewarding greatness</tspan>
  </text>
  <text class="service-text blue">
    <tspan x="312" y="883">Remuneration and</tspan>
    <tspan x="312" y="906">incentive schemes</tspan>
  </text>
</svg>
</body>
</html>
```